Copperleaf Roofing Business Card

This is my current business card. But I’d like to make some changes. Somewhere on the card I’d like to list some of the services we offer. Maybe on the back? But I’d still like to keep the red. White and black modern look.

-residential & commercial roofing
-Roof Repairs & Maintenance
-Storm Damage & Insurance Claims specialist
-Christmas Lights and permanent Christmas lights
Fencing. Windows. Gutters. Siding. Sheetrock, painting.

```html
<!DOCTYPE html>
<html lang="en">
<head>
<meta charset="utf-8">
<title>Copperleaf Roofing Co. – Business Card</title>
<link rel="stylesheet" href="https://fonts.googleapis.com/css2?family=Lato:wght@400;700;900&family=Michroma&display=swap">
<style>
  :root {
    --stage: #2b2b2d;
    --red: #e21f26;
    --red-deep: #8e1015;
    --red-dark: #5e0b0e;
    --black: #111111;
    --white: #ffffff;
    --ink: #1a1a1a;
  }
  * { box-sizing: border-box; margin: 0; padding: 0; }
  html, body {
    width: 1200px; height: 694px; overflow: hidden;
    background: var(--stage);
  }
  .canvas {
    position: relative; width: 1200px; height: 694px;
    display: flex; align-items: center; justify-content: center; gap: 40px;
  }
  .card {
    position: relative; width: 540px; height: 309px;
    border-radius: 16px; overflow: hidden;
    box-shadow: 0 10px 30px rgba(0,0,0,.45);
  }

  /* Front */
  .card--front { background: var(--red-deep); }
  .tartan-field {
    position: absolute; inset: 0;
    background:
      linear-gradient(135deg, rgba(255,255,255,0) 38%, rgba(255,255,255,.18) 44%, rgba(255,255,255,0) 50%),
      linear-gradient(160deg, var(--red) 0%, var(--red-deep) 45%, var(--red-dark) 75%, var(--black) 100%);
  }
  .front-brand {
    position: absolute; inset: 0;
    display: flex; flex-direction: column; align-items: center; justify-content: center; gap: 18px;
  }
  .brand-disc {
    width: 96px; height: 96px; border-radius: 50%;
    background: var(--red-dark); border: 4px solid var(--white);
  }
  .brand-name {
    font-family: "Lato", sans-serif; font-weight: 900;
    text-transform: uppercase; text-align: center; line-height: 1.05;
  }
  .front-brand .brand-name { color: var(--white); font-size: 34px; letter-spacing: 2px; }

  /* Back */
  .card--back { background: var(--white); }
  .back-top {
    position: absolute; left: 0; right: 0; top: 26px; height: 140px;
    display: flex; align-items: center;
  }
  .back-brand {
    width: 215px; display: flex; flex-direction: column; align-items: center; gap: 10px;
  }
  .back-brand .brand-disc { width: 64px; height: 64px; border: none; background: var(--red); }
  .back-brand .brand-name { color: var(--red); font-size: 19px; letter-spacing: 1px; }
  .divider { width: 1.5px; height: 120px; background: var(--red); margin-right: 26px; }
  .contact { flex: 1; }
  .person-name {
    font-family: "Michroma", sans-serif; font-size: 20px; letter-spacing: 1px;
    color: var(--ink); text-transform: uppercase;
  }
  .person-name .first { color: var(--red); }
  .person-role { font-family: "Lato", sans-serif; font-size: 14px; color: var(--ink); margin: 2px 0 10px; }
  .contact-list { list-style: none; font-family: "Lato", sans-serif; font-size: 13.5px; color: var(--ink); }
  .contact-list li { display: flex; align-items: center; gap: 8px; margin-bottom: 4px; }
  .contact-list svg { width: 14px; height: 14px; flex: none; }

  .services {
    position: absolute; left: 30px; right: 24px; top: 186px;
    list-style: none;
    font-family: "Lato", sans-serif; font-size: 14px; line-height: 1.5; color: var(--ink);
  }
  .services li::before, .services .sep::before {
    content: "•"; color: var(--red); font-weight: 900; margin: 0 5px 0 0;
  }
  .services .sep::before { margin: 0 5px; }
  .tartan-strip {
    position: absolute; left: 0; right: 0; bottom: 0; height: 16px;
    background: linear-gradient(90deg, var(--red-dark), var(--red), var(--red-deep), var(--black), var(--red));
  }
</style>
</head>
<body>
<main class="canvas">

  <section class="card card--front">
    <div class="tartan-field" role="img" aria-label="Red, black and white tartan plaid pattern"></div>
    <div class="front-brand">
      <span class="brand-disc"></span>
      <p class="brand-name">Copperleaf<br>Roofing Co.</p>
    </div>
  </section>

  <section class="card card--back">
    <div class="back-top">
      <div class="back-brand">
        <span class="brand-disc"></span>
        <p class="brand-name">Copperleaf<br>Roofing Co.</p>
      </div>
      <span class="divider"></span>
      <div class="contact">
        <h1 class="person-name"><span class="first">Dana</span> Whitfield</h1>
        <p class="person-role">Owner</p>
        <ul class="contact-list">
          <li>
            <svg viewBox="0 0 16 16" aria-hidden="true"><path fill="#e21f26" d="M3.6 1.5l2.3 2.6-1.3 1.8c.9 2 2.5 3.6 4.5 4.5l1.8-1.3 2.6 2.3-1.4 2.1C7 13.3 2.7 9 1.5 2.9z"/></svg>
            682-555-0148
          </li>
          <li>
            <svg viewBox="0 0 16 16" aria-hidden="true"><rect x="1" y="3" width="14" height="10" fill="#e21f26"/><path d="M1.5 3.5L8 9l6.5-5.5" stroke="#fff" stroke-width="1.4" fill="none"/></svg>
            dana@copperleafroofing.co
          </li>
          <li>
            <svg viewBox="0 0 16 16" aria-hidden="true"><circle cx="8" cy="8" r="7" fill="#e21f26"/><g stroke="#fff" stroke-width="1" fill="none"><ellipse cx="8" cy="8" rx="3" ry="6.5"/><path d="M1.5 8h13M2.5 4.8h11M2.5 11.2h11"/></g></svg>
            www.copperleafroofing.co
          </li>
        </ul>
      </div>
    </div>

    <ul class="services">
      <li>Residential &amp; commercial roofing<span class="sep">Roof Repairs &amp; Maintenance</span></li>
      <li>Storm Damage &amp; Insurance Claims specialist</li>
      <li>Christmas Lights and permanent Christmas lights</li>
      <li>Fencing<span class="sep">Windows</span><span class="sep">Gutters</span><span class="sep">Siding</span><span class="sep">Sheetrock</span><span class="sep">Painting</span></li>
    </ul>

    <div class="tartan-strip" role="img" aria-label="Narrow band of red and black tartan plaid"></div>
  </section>

</main>
</body>
</html>
```